KTWG application splash screen

We need a 1024x768 image for use as an application splash screen.
The image will be displayed full screen on an 10 inch industrial PC 1024x768 screen while our application is launching. The image should convey that the application is "Waiting for connection to Wi-Fi access point..." and include a graphic of the industrial PC connected to the access point via an Ethernet cable. A list of troubleshooting steps should be included at the bottom of the image. The troubleshooting steps should not be the main focus of the image and should be shown in a smaller font (but still readable at 1024x768 displayed on a 10 inch screen).
I will include a mock up of the general idea of what we are looking for as well as image files for the industrial PC, a screenshot of our application to show on the PC's screen and the AP.
For general look and feel and a sense of corporate branding please review our website https://marrowgatesoilworks.example/. The splash screen should reflect corporate branding.
Target Market(s)
Users of our application
Industry/Entity Type
Agriculture
Look and feel

```html
<!DOCTYPE html>
<html lang="en">
<head>
<meta charset="utf-8">
<title>KTWG splash screen – Waiting for Wi-Fi</title>
<link href="https://fonts.googleapis.com/css2?family=Poppins:wght@400;500;600;700&display=swap" rel="stylesheet">
<style>
  :root {
    --brand-green: #2ab673;
    --ink: #2f2f2f;
    --ink-dark: #1e1e1e;
    --paper: #ffffff;
    --device-body: #3a3a3a;
    --device-screen: #e9eeeb;
    --ap-body: #f2f2f2;
    --cable: #111111;
  }
  * { box-sizing: border-box; margin: 0; padding: 0; }
  html, body {
    width: 1200px; height: 1200px; overflow: hidden;
    background: var(--paper);
    font-family: "Poppins", sans-serif;
  }
  .splash {
    position: absolute; left: 0; top: 150px;
    width: 1200px; height: 900px;
    background: var(--paper);
    overflow: hidden;
  }
  .hero {
    position: absolute; left: 0; top: 0;
    width: 1200px; height: 710px;
    background: var(--brand-green);
    border-radius: 0 0 134px 134px;
  }
  .headline {
    position: absolute; left: 0; top: 146px; width: 100%;
    text-align: center; color: var(--paper);
    font-weight: 500; font-size: 64px; line-height: 66px;
    letter-spacing: 0.2px;
  }
  .industrial-pc {
    position: absolute; left: 273px; top: 398px;
    width: 187px; height: 144px;
    border-radius: 10px;
    background: var(--device-body);
    box-shadow: inset 0 0 0 8px #2a2a2a;
  }
  .industrial-pc::after {
    content: ""; position: absolute;
    left: 16px; top: 12px; right: 16px; bottom: 22px;
    background: var(--device-screen); border-radius: 2px;
  }
  .access-point {
    position: absolute; left: 884px; top: 359px;
    width: 25px; height: 189px;
    border-radius: 6px;
    background: linear-gradient(90deg, #dcdcdc, var(--ap-body) 50%, #d6d6d6);
  }
  .ethernet-cable { position: absolute; left: 0; top: 0; }
  .help {
    position: absolute; left: 53px; top: 732px;
    color: var(--ink);
  }
  .help-tag {
    display: inline-block;
    width: 178px; height: 26px; line-height: 26px;
    background: var(--brand-green); color: var(--paper);
    border-radius: 7px; text-align: center;
    font-size: 13px; font-weight: 400;
  }
  .help-note {
    display: flex; align-items: center; gap: 5px;
    font-size: 13.5px; font-weight: 600;
    margin-left: 8px; line-height: 24px;
  }
  .help-note:first-of-type { margin-top: 4px; }
  .help-note svg { flex: none; }
  .help-steps {
    list-style: none; margin-left: 26px;
    font-size: 11.6px; font-weight: 600; line-height: 16.5px;
  }
  .help-steps li::before { content: "• "; }
  .brand {
    position: absolute; left: 914px; top: 742px; width: 240px;
    color: var(--ink-dark); font-weight: 700;
  }
  .brand-name { font-size: 60px; line-height: 64px; letter-spacing: 1px; }
  .brand-full { font-size: 15px; line-height: 22px; margin-top: 4px; }
</style>
</head>
<body>
  <main class="splash">
    <section class="hero">
      <h1 class="headline">Waiting for connection to<br>Wi-Fi access point...</h1>

      <svg class="ethernet-cable" width="1200" height="710" aria-hidden="true">
        <path d="M442 540 V552 Q442 560 450 560 H888 Q896 560 896 552 V546"
              fill="none" stroke="var(--cable)" stroke-width="2.5"/>
      </svg>

      <div class="industrial-pc" role="img" aria-label="Industrial tablet PC showing the seeding monitor application"></div>
      <div class="access-point" role="img" aria-label="Outdoor Wi-Fi access point with two antennas and a green status light"></div>
    </section>

    <section class="help">
      <span class="help-tag">Troubleshooting steps:</span>
      <p class="help-note">
        <svg width="14" height="14" viewBox="0 0 14 14" aria-hidden="true">
          <circle cx="7" cy="7" r="6" fill="none" stroke="var(--brand-green)" stroke-width="1.2"/>
          <rect x="6.3" y="3" width="1.4" height="5.2" fill="var(--brand-green)"/>
          <rect x="6.3" y="9.4" width="1.4" height="1.4" fill="var(--brand-green)"/>
        </svg>
        This screen should only be visible for a short time on boot.
      </p>
      <p class="help-note">
        <svg width="14" height="14" viewBox="0 0 14 14" aria-hidden="true">
          <circle cx="7" cy="7" r="6" fill="none" stroke="var(--brand-green)" stroke-width="1.2"/>
          <rect x="6.3" y="3" width="1.4" height="5.2" fill="var(--brand-green)"/>
          <rect x="6.3" y="9.4" width="1.4" height="1.4" fill="var(--brand-green)"/>
        </svg>
        If this screen stays visible for more than a minute:
      </p>
      <ul class="help-steps">
        <li>Verify that the Wi-Fi Access Point (AP) powers up when this system does (indicated by a green light on the side of the AP).</li>
        <li>Check the Ethernet cable between this system and the AP for damage, and replace it if necessary.</li>
        <li>Power-cycle this system and wait for it to reboot fully.</li>
        <li>If the issue persists, contact KTWG support for further assistance.</li>
      </ul>
    </section>

    <div class="brand">
      <div class="brand-name">KTWG</div>
      <div class="brand-full">Marrowgate Soil Works Inc.</div>
    </div>
  </main>
</body>
</html>
```